Small corporate website template design

I need a couple templates designed for a small corporate website. The corporate site reflects the existence of the parent company which will own various brands/services that have their own websites, so it will mainly be used to present who we are, what we do, what is happening (news/events), how to contact us, link off to our other brand/service sites, as well as post information for public relations, investors, and job opportunities.

The company name is Brelvanto LLC (www.brelvanto-example.com), and the name is representative of stratified layers of interconnected digital services. The corporate site is not expected to generate a bunch of fanfare - that honor will be reserved for the externally linked brand/service sites.

The provided logo may be manipulated in color, size, shape, positioning, etc. to get it to fit with the design, but should be integrated in some way.

What we are looking for is a home page layout as well as a template for an inner page whereby the navigation/logo, etc may be diminished to some extent for the inner pages. We are also interested in reusable elements such as dividers, content containers, etc. in order to represent the types of information described above that we would like to present as described above.

We are particularly interested in consistency of design elements, conservative use of color (including consideration of accessibility concerns), judicious use of whitespace in favor of simplified messaging, and something lending itself well to internationalization/translation.

Target Market(s)

Small business owners, entrepreneurs (B2B)

Number of Pages Required

2 page

Font styles to use
Sans Serif

Requirements
Must have
• See the attached PDF with the logo concept, color swatches, and comparative sites.

```html
<!DOCTYPE html>
<html lang="en">
<head>
<meta charset="utf-8">
<title>Brelvanto LLC — Home</title>
<link href="https://fonts.googleapis.com/css2?family=Roboto+Condensed:wght@300;400;700&family=Open+Sans:wght@400;600&family=Roboto:wght@400;500&display=swap" rel="stylesheet">
<style>
:root{
  --navy:#1a3d7c;
  --navy-deep:#12306a;
  --orange:#e8812b;
  --ink:#1d1d1f;
  --text:#3a3a3a;
  --white:#ffffff;
  --black:#0f0f10;
  --sky:#dde7f2;
  --sky-soft:#eef3f9;
  --line:#3a3a3d;
}
*{margin:0;padding:0;box-sizing:border-box}
html,body{width:1200px;height:2250px;overflow:hidden}
body{position:relative;background:var(--white);font-family:"Open Sans",Arial,sans-serif;color:var(--text)}
.page-bg{position:absolute;inset:0;background:linear-gradient(180deg,var(--sky) 0%,var(--white) 16%,var(--white) 60%,var(--sky-soft) 74%,#d6e2ef 84%)}
.shapes{position:absolute;left:0;top:0}
.brand{position:absolute;left:88px;top:58px;display:flex;align-items:center;gap:10px;font-family:"Roboto",Arial,sans-serif;font-size:22px;font-weight:500;color:var(--black)}
.brand-dot{width:16px;height:16px;border-radius:50%;background:var(--black)}
.phone{position:absolute;left:952px;top:32px;display:flex;align-items:center;gap:6px;font-family:"Roboto Condensed",Arial,sans-serif;font-size:21px;color:var(--ink)}
.main-nav{position:absolute;left:529px;top:72px;display:flex;gap:35px;font-family:"Roboto",Arial,sans-serif;font-size:17px;color:var(--ink)}
.main-nav .is-active{color:var(--orange)}
.hero-art{position:absolute;left:62px;top:130px;width:480px;height:570px;border-radius:12px;background:radial-gradient(circle at 50% 45%,#c9d9f0 0%,#e6eefa 55%,rgba(255,255,255,0) 80%)}
.hero-kicker{position:absolute;left:614px;top:344px;font-family:"Roboto Condensed",Arial,sans-serif;font-size:33px;font-weight:400;color:var(--orange)}
.hero-title{position:absolute;left:612px;top:388px;font-family:"Roboto Condensed",Arial,sans-serif;font-size:55px;font-weight:400;color:var(--ink)}
.watch{position:absolute;left:620px;top:471px;display:flex;align-items:center;gap:18px;font-family:"Roboto",Arial,sans-serif;font-size:16px;color:var(--ink)}
.watch-btn{width:46px;height:46px;border-radius:50%;background:var(--white);box-shadow:0 4px 14px rgba(0,0,0,.16);display:flex;align-items:center;justify-content:center}
.about{position:absolute;left:0;top:800px;width:1200px;text-align:center;color:var(--white)}
.about h2{font-family:"Roboto Condensed",Arial,sans-serif;font-size:50px;font-weight:400;margin-bottom:14px}
.about p{width:712px;margin:0 auto;font-size:14.5px;line-height:27.5px}
.btn-outline{display:inline-block;margin-top:28px;padding:8px 22px;border:1.5px solid var(--white);border-radius:20px;font-size:14.5px;color:var(--white)}
.section-title{position:absolute;font-family:"Roboto",Arial,sans-serif;font-size:27px;font-weight:400;color:var(--ink)}
.blog-list{position:absolute;left:92px;top:1383px;width:484px}
.blog-card{display:flex;height:129px;margin-bottom:12px;background:var(--white);border:1px solid #c9c9c9;box-shadow:0 2px 6px rgba(0,0,0,.08)}
.blog-thumb{width:130px;flex:none}
.thumb-a{background:linear-gradient(135deg,#1c2530,#4a5560 60%,#1a1f26)}
.thumb-b{background:radial-gradient(circle,#7a1a24 0%,#2a1418 50%,#111 100%)}
.thumb-c{background:radial-gradient(circle at 45% 50%,#3d86c8 0%,#0f2d55 55%,#071426 100%)}
.blog-body{padding:14px 20px 0 24px}
.blog-body h3{font-family:"Roboto",Arial,sans-serif;font-size:18px;font-weight:400;color:var(--ink);margin-bottom:6px}
.blog-body p{font-size:13.5px;line-height:22px;color:var(--text)}
.view-more{position:absolute;font-family:"Roboto",Arial,sans-serif;font-size:14px;color:var(--ink)}
.feature-card{position:absolute;left:626px;top:1386px;width:480px;height:406px;background:var(--white);border:1px solid #c9c9c9;box-shadow:0 2px 6px rgba(0,0,0,.08)}
.feature-media{position:relative;height:278px;background:linear-gradient(120deg,#2e3c4c 0%,#8a9aab 45%,#f0c89a 70%,#5a6b7d 100%)}
.play{position:absolute;left:214px;top:114px;width:56px;height:56px;border-radius:50%;background:rgba(20,20,20,.55);border:2px solid rgba(255,255,255,.8);display:flex;align-items:center;justify-content:center}
.feature-body{padding:20px 28px 0 28px}
.feature-body h3{font-family:"Roboto",Arial,sans-serif;font-size:18px;font-weight:400;color:var(--ink);margin-bottom:6px}
.feature-body p{font-size:13.5px;line-height:22px}
.footer-brand{position:absolute;left:100px;top:2095px;display:flex;align-items:center;gap:10px;font-family:"Roboto",Arial,sans-serif;font-size:21px;font-weight:500;color:var(--white)}
.footer-brand .brand-dot{background:var(--white)}
.social{position:absolute;left:968px;top:1970px;display:flex;gap:14px}
.social span{width:24px;height:24px;border-radius:4px;background:#b9b9bc}
.newsletter{position:absolute;left:616px;top:2069px;display:flex;align-items:center;gap:20px}
.newsletter label{font-family:"Roboto",Arial,sans-serif;font-size:17px;color:var(--white);letter-spacing:.3px}
.email-field{width:282px;height:52px;border:1.5px solid var(--white);border-radius:26px;display:flex;align-items:center;justify-content:space-between;padding:0 18px 0 24px;font-size:13px;color:#9a9a9a}
.footer-rule{position:absolute;left:88px;top:2161px;width:1025px;height:1px;background:var(--line)}
.footer-nav{position:absolute;left:90px;top:2192px;display:flex;gap:28px;font-family:"Roboto",Arial,sans-serif;font-size:13px;color:var(--white)}
.copyright{position:absolute;left:870px;top:2193px;font-family:"Roboto",Arial,sans-serif;font-size:13px;color:var(--white)}
</style>
</head>
<body>
<div class="page-bg"></div>

<svg class="shapes" width="1200" height="2250" viewBox="0 0 1200 2250" aria-hidden="true">
  <defs>
    <linearGradient id="bandFill" x1="0" y1="0" x2="1" y2="1">
      <stop offset="0" stop-color="#1d4286"/>
      <stop offset="1" stop-color="#163a78"/>
    </linearGradient>
  </defs>
  <polygon points="0,777 1200,575 1200,1072 0,1275" fill="url(#bandFill)"/>
  <polygon points="0,1995 1200,1880 1200,2250 0,2250" fill="var(--black)"/>
</svg>

<header>
  <div class="brand"><span class="brand-dot"></span>Brelvanto</div>
  <div class="phone">
    <svg width="16" height="16" viewBox="0 0 24 24" aria-hidden="true"><path fill="#e8812b" d="M6.6 10.8a15.1 15.1 0 0 0 6.6 6.6l2.2-2.2c.3-.3.7-.4 1-.2 1.1.4 2.3.6 3.6.6.6 0 1 .4 1 1V20c0 .6-.4 1-1 1A17 17 0 0 1 3 4c0-.6.4-1 1-1h3.5c.6 0 1 .4 1 1 0 1.3.2 2.5.6 3.6.1.3 0 .7-.2 1z"/></svg>
    555-014-2290
  </div>
  <nav class="main-nav">
    <span class="is-active">Home</span><span>About us</span><span>Services</span><span>Investors</span><span>News</span><span>Contact us</span>
  </nav>
</header>

<section class="hero">
  <div class="hero-art" role="img" aria-label="Isometric illustration of people working with screens and devices on stacked platforms"></div>
  <p class="hero-kicker">Adaptive Software Technology for</p>
  <h1 class="hero-title">The Digital Revolution</h1>
  <div class="watch">
    <span class="watch-btn"><svg width="14" height="16" viewBox="0 0 14 16" aria-hidden="true"><polygon points="1,1 13,8 1,15" fill="#e8812b"/></svg></span>
    WATCH VIDEO
  </div>
</section>

<section class="about">
  <h2>Who We Are</h2>
  <p>It is a long established fact that a reader will be distracted by the readable content of a page when looking at its layout. The point of using Lorem Ipsum is that it has a more-or-less normal distribution of letters, as opposed to using 'Content here, content here', making it look like readable English. Many desktop publishing packages and web page editors now use Lorem Ipsum as their default model text, Many desktop publishing packages and web page editors now use Lorem Ipsum as their default model</p>
  <span class="btn-outline">Read More »</span>
</section>

<h2 class="section-title" style="left:95px;top:1327px">Latest Blog</h2>
<div class="blog-list">
  <article class="blog-card">
    <div class="blog-thumb thumb-a" role="img" aria-label="Photo of a dark technology workspace"></div>
    <div class="blog-body"><h3>Neque porro quisquam</h3><p>The point of using Lorem Ipsum is that it has a more-or-less normal distribution of letters, as opposed to using 'Content here,</p></div>
  </article>
  <article class="blog-card">
    <div class="blog-thumb thumb-b" role="img" aria-label="Image of a glowing red wireframe cube"></div>
    <div class="blog-body"><h3>Neque porro quisquam</h3><p>The point of using Lorem Ipsum is that it has a more-or-less normal distribution of letters, as opposed to using 'Content here,</p></div>
  </article>
  <article class="blog-card">
    <div class="blog-thumb thumb-c" role="img" aria-label="Image of a digital globe with network lights"></div>
    <div class="blog-body"><h3>Neque porro quisquam</h3><p>The point of using Lorem Ipsum is that it has a more-or-less normal distribution of letters, as opposed to using 'Content here,</p></div>
  </article>
</div>
<span class="view-more" style="left:485px;top:1810px">View More »</span>

<h2 class="section-title" style="left:633px;top:1320px">What we do</h2>
<article class="feature-card">
  <div class="feature-media" role="img" aria-label="Video still of hands working with a tablet and laptop">
    <span class="play"><svg width="18" height="20" viewBox="0 0 18 20" aria-hidden="true"><polygon points="2,1 17,10 2,19" fill="#ffffff"/></svg></span>
  </div>
  <div class="feature-body"><h3>Quisquam est qui dolorem ipsum</h3><p>The point of using Lorem Ipsum is that it has a more-or-less normal distribution of letters, as opposed to using 'Content here,</p></div>
</article>
<span class="view-more" style="left:1018px;top:1810px">View More »</span>

<footer>
  <div class="footer-brand"><span class="brand-dot"></span>Brelvanto</div>
  <div class="social" aria-label="Social links"><span></span><span></span><span></span><span></span></div>
  <div class="newsletter">
    <label>JOIN OUR NEWSLETTER</label>
    <div class="email-field">Email address
      <svg width="16" height="16" viewBox="0 0 16 16" aria-hidden="true"><circle cx="8" cy="8" r="8" fill="#cfcfcf"/><path d="M8 4v8M4 8h8" stroke="#0f0f10" stroke-width="2"/></svg>
    </div>
  </div>
  <div class="footer-rule"></div>
  <nav class="footer-nav"><span>Home</span><span>About us</span><span>Services</span><span>Investors</span><span>News</span><span>Contact us</span></nav>
  <p class="copyright">Copyright © 2018. All Rights Reserved</p>
</footer>
</body>
</html>
```